Quorva - corporate Business Card

We need a good look and innovative business card for a new start up company based in Los Angeles called "Quorva". We are in a payment business, including payment card, app, and ewallet. We are expert in online payment and Card not present (CNP) transaction.
We need an innovative, modern business card.

Our logo font is Aero Matics

Target Market(s)

Startup - Bank - Online Payment - Card Manufacturing

Industry/Entity Type

Startup

Contact Information for Business Card

phone: 555 014 7396 - Address: 4172 Marlowe blvd, Brenhollow, CA 90299

Requirements
Must have
• Message: innovative, professional, expert, high tech, trust, online payment expert, security
Nice to have
• no comment
Should not have
• no Comment

```html
<!DOCTYPE html>
<html lang="en">
<head>
<meta charset="utf-8">
<title>Quorva – Business Card</title>
<link href="https://fonts.googleapis.com/css2?family=Open+Sans:wght@400;600;700&display=swap" rel="stylesheet">
<style>
  :root {
    --brand-red: #b81f2e;
    --brand-red-deep: #ad1c2a;
    --divider-grey: #9b9b9b;
    --text-grey: #9a9a9a;
    --paper: #ffffff;
    --blush: #f5e4de;
    --backdrop: #2b2b2d;
  }
  * { box-sizing: border-box; margin: 0; padding: 0; }
  html, body { width: 1200px; height: 880px; overflow: hidden; }
  body {
    background: var(--backdrop);
    font-family: "Open Sans", Arial, sans-serif;
    position: relative;
  }
  .card {
    position: absolute;
    width: 620px;
    height: 354px;
    border-radius: 22px;
    overflow: hidden;
    box-shadow: 0 14px 30px rgba(0,0,0,0.45);
  }
  /* Front */
  .card-front {
    left: 150px;
    top: 70px;
    background: var(--brand-red);
  }
  .card-front .halo {
    position: absolute;
    width: 440px;
    height: 440px;
    border-radius: 50%;
    background: var(--brand-red-deep);
    left: -70px;
    top: 70px;
  }
  .card-front .wordmark {
    position: absolute;
    left: 200px;
    top: 118px;
    font-size: 84px;
    font-weight: 700;
    letter-spacing: 1px;
    color: var(--paper);
    line-height: 1;
  }
  /* Back */
  .card-back {
    left: 430px;
    top: 460px;
    background: var(--paper);
  }
  .card-back .band {
    position: absolute;
    left: 0; top: 0;
    width: 100%;
    height: 150px;
    background: var(--brand-red);
    z-index: 2;
  }
  .card-back .band-rule {
    position: absolute;
    left: 0; top: 150px;
    width: 100%;
    height: 9px;
    background: var(--divider-grey);
    z-index: 2;
  }
  .card-back .accent-circle {
    position: absolute;
    width: 280px;
    height: 280px;
    border-radius: 50%;
    background: var(--blush);
    left: 400px;
    top: 110px;
  }
  .card-back .wordmark {
    position: absolute;
    z-index: 3;
    left: 40px;
    top: 76px;
    font-size: 62px;
    font-weight: 700;
    letter-spacing: 1px;
    color: var(--paper);
    line-height: 1;
  }
  .card-back .holder {
    position: absolute;
    z-index: 3;
    right: 36px;
    top: 42px;
    text-align: right;
    color: var(--paper);
  }
  .holder .name { font-size: 19px; font-weight: 700; line-height: 1.1; }
  .holder .role { font-size: 14px; font-weight: 400; line-height: 1.2; }
  .contact {
    position: absolute;
    left: 60px;
    top: 208px;
    color: var(--text-grey);
    font-size: 16px;
    line-height: 1.3;
    z-index: 3;
  }
  .contact .address { margin-bottom: 14px; }
  .contact .line { display: flex; align-items: center; gap: 10px; }
  .contact .line + .line { margin-top: 2px; }
  .icon { width: 20px; height: 20px; flex: none; }
</style>
</head>
<body>

  <section class="card card-front" aria-label="Card front">
    <div class="halo"></div>
    <div class="wordmark">quorva</div>
  </section>

  <section class="card card-back" aria-label="Card back">
    <div class="accent-circle"></div>
    <div class="band"></div>
    <div class="band-rule"></div>
    <div class="wordmark">quorva</div>
    <div class="holder">
      <div class="name">Lena Varrick</div>
      <div class="role">Managing Director</div>
    </div>
    <div class="contact">
      <div class="address">4172 Marlowe blvd,<br>Brenhollow, CA 90299</div>
      <div class="line">
        <svg class="icon" viewBox="0 0 20 20" aria-hidden="true">
          <circle cx="10" cy="10" r="10" fill="#b81f2e"/>
          <path d="M6.2 5.5c.5-.4 1.2-.3 1.5.2l1 1.6c.3.5.2 1-.2 1.3l-.6.4c.5 1.1 1.4 2 2.5 2.5l.4-.6c.3-.4.9-.5 1.3-.2l1.6 1c.5.3.6 1 .2 1.5l-.6.7c-.6.7-1.7.8-2.6.3-2.1-1.1-3.8-2.8-4.9-4.9-.5-.9-.4-2 .3-2.6z" fill="#fff"/>
        </svg>
        <span>555 014 7396</span>
      </div>
      <div class="line">
        <svg class="icon" viewBox="0 0 20 20" aria-hidden="true">
          <circle cx="10" cy="10" r="10" fill="#b81f2e"/>
          <rect x="5" y="6.5" width="10" height="7" rx="1" fill="#fff"/>
          <path d="M5.3 7l4.7 3.6L14.7 7" fill="none" stroke="#b81f2e" stroke-width="1.1"/>
        </svg>
        <span>hello@quorvamail.com</span>
      </div>
    </div>
  </section>

</body>
</html>
```